5-6 page Website Design- Harbor Lantern Program, including 2 videos

We need an elegantly simple and beautiful website for the Harbor Lantern Program (HLP), a 6-month program for founders and leaders of startups who want to shift from Actors to Authors in their leadership.
At a minimum, the website will include:
Home Page
Program Description--Why Actor to Author?
Program Timeline and Structure
Testimonials and Past Clients (this page will include a testimonials video and text)
Team
FAQs
I'd like to see two versions of The Home Page/Landing Page:
1. Just an image with the words
If your startup is growing rapidly,
we can help you do the same.
HLP: The ACTOR to AUTHOR Shift
2. A place for a video describing the program
No payment integration on the website. Just information.
Startup founders and senior leaders

```html
<!DOCTYPE html>
<html lang="en">
<head>
<meta charset="utf-8">
<title>Harbor Lantern Program – Website Design</title>
<link href="https://fonts.googleapis.com/css2?family=Gilda+Display&family=Raleway:wght@500;600&family=IBM+Plex+Sans:wght@400;500;600;700&display=swap" rel="stylesheet">
<style>
:root{
  --board:#d8d9da;
  --navy:#123a78;
  --navy-deep:#0d2a63;
  --blue:#2f8fd6;
  --ink:#2b2b2b;
  --muted:#555;
  --paper:#ffffff;
  --mist:#f1f1f7;
  --footer:#1c1c1c;
}
*{box-sizing:border-box;margin:0;padding:0}
html,body{width:1200px;height:3909px;overflow:hidden}
body{background:var(--board);position:relative;font-family:"IBM Plex Sans",sans-serif;color:var(--ink)}
.page{position:absolute;left:94px;width:1035px;overflow:hidden}
.brand{position:absolute;display:flex;align-items:center;gap:10px}
.brand-dot{width:62px;height:62px;border-radius:50%;background:var(--blue)}
.brand-name{font-family:"Raleway",sans-serif;font-weight:600;font-size:17px;line-height:18px;text-transform:uppercase;color:var(--blue);border-left:2px solid var(--blue);padding-left:10px}
.btn{display:inline-block;background:var(--navy);color:#fff;font-size:12px;letter-spacing:.3px;padding:7px 17px;border-radius:4px}
.photo{position:absolute}

/* Page 1 */
.p1{top:141px;height:621px}
.p1 .photo-bg{inset:0;background:linear-gradient(180deg,#6e9cc7 0%,#a8c4dc 35%,#c9d6de 55%,#6d7f86 80%,#3e4a4c 100%)}
.intro-box{position:absolute;left:58px;top:177px;width:927px;height:381px;background:rgba(255,255,255,.78)}
.intro-box h2{position:absolute;left:33px;top:20px;font-family:"Gilda Display",serif;font-weight:400;font-size:32px;color:#222}
.intro-text{position:absolute;left:33px;top:76px;width:413px;font-size:10.6px;line-height:15.4px;text-align:justify;color:#333}
.intro-text p+p{margin-top:14px}
.intro-box .btn{position:absolute;left:33px;top:320px}
.video{position:absolute;left:478px;top:32px;width:422px;height:320px;background:linear-gradient(135deg,#8a6a5a,#c9b8a6 50%,#6f6a66)}
.play{position:absolute;left:50%;top:50%;transform:translate(-50%,-50%)}

/* Page 2 */
.p2{top:816px;height:621px}
.p2 .photo-bg{inset:0;background:radial-gradient(ellipse at 55% 70%,#7c8a6a 0%,#3f4c34 45%,#1f2a1c 100%)}
.landing-line{position:absolute;left:0;right:0;top:117px;text-align:center;font-family:"Gilda Display",serif;font-size:35px;line-height:43px;color:#fff}

/* Page 3 */
.p3{top:1494px;height:2318px;background:var(--paper)}
.hero{position:absolute;left:0;top:0;width:1035px;height:524px;background:linear-gradient(180deg,#b9c3cf 0%,#cdb9a4 30%,#d69a5e 50%,#7a4a2a 75%,#2e2622 100%)}
.nav{position:absolute;left:337px;top:31px;display:flex;gap:20px;font-size:11.5px;color:#222;align-items:center}
.nav .on{background:var(--navy);color:#fff;padding:4px 8px;border-radius:3px}
.hero-title{position:absolute;left:0;right:0;top:108px;text-align:center;font-family:"Raleway",sans-serif;font-weight:500;font-size:31px;line-height:38px;color:var(--navy)}
.hero-btn{position:absolute;left:460px;top:162px}
.dots{position:absolute;left:490px;top:486px;display:flex;gap:5px}
.dots i{width:6px;height:6px;background:#fff;display:block}
.dots i.on{background:transparent;border:1px solid #fff}

.sec-title{position:absolute;left:0;right:0;text-align:center;font-family:"Raleway",sans-serif;font-weight:500;font-size:22px;color:var(--navy)}
.rule{position:absolute;left:50%;width:38px;height:2px;background:var(--navy);transform:translateX(-50%)}

.timeline{position:absolute;top:524px;left:0;width:1035px;height:414px}
.t-card{position:absolute;top:103px;width:256px;height:262px;background:#fff;border:1px solid #c9d3e3;border-bottom:3px solid var(--navy);text-align:center}
.t-head{height:53px;background:linear-gradient(90deg,#0f3f82,#1f68a8 50%,#0f3f82);color:#fff;font-weight:700;font-size:14px;line-height:53px}
.t-body{padding-top:20px}
.t-week{display:inline-block;border:1px solid #2f6fb0;color:#2f6fb0;font-size:10.5px;padding:1px 6px;margin-top:10px}
.t-item{font-size:12.5px;color:#222;margin-top:6px}
.arrow{position:absolute;top:218px}

.logic{position:absolute;top:938px;left:0;width:1035px;height:402px;background:var(--mist)}
.logic .photo{left:0;top:0;width:482px;height:402px;background:linear-gradient(90deg,#7d5a4c,#b9a394 55%,#e6e3e8 100%)}
.logic h3{position:absolute;left:520px;top:33px;font-family:"Raleway",sans-serif;font-weight:500;font-size:23px;color:var(--navy)}
.logic .l-rule{position:absolute;left:520px;top:72px;width:38px;height:2px;background:var(--navy)}
.logic-text{position:absolute;left:522px;top:96px;width:400px;font-size:11.2px;line-height:15.2px;text-align:justify;color:#333}
.logic-text p+p{margin-top:14px}
.logic .btn{position:absolute;left:522px;top:335px}

.team{position:absolute;top:1340px;left:0;width:1035px;height:459px}
.m-card{position:absolute;top:114px;width:196px;height:297px;background:#fff;box-shadow:0 2px 8px rgba(0,0,0,.12);text-align:center}
.m-card .photo{position:relative;height:135px}
.m-name{font-weight:600;font-size:12px;margin-top:14px;color:#222}
.m-role{font-size:12px;color:#333;margin-top:2px}
.m-bio{font-size:10px;line-height:13.5px;color:#444;margin:8px 22px 0}
.m-card .btn{font-size:10.5px;padding:3px 12px;margin-top:14px}

.testi{position:absolute;top:1799px;left:0;width:1035px;height:333px;background:radial-gradient(ellipse at 50% 110%,#2050a6 0%,#0e2f6e 55%,#0b285f 100%);color:#fff}
.testi .sec-title{color:#fff;top:44px}
.testi .rule{background:#fff;top:88px}
.testi-text{position:absolute;left:170px;width:695px;top:116px;text-align:center;font-size:14px;line-height:23px;color:#e8eefb}
.avatar{position:absolute;left:497px;top:250px;width:42px;height:42px;border-radius:50%;background:linear-gradient(#c9d3e0,#7f93ad);border:2px solid #fff}
.testi-name{position:absolute;left:0;right:0;top:294px;text-align:center;font-weight:600;font-size:13px}

.footer{position:absolute;top:2132px;left:0;width:1035px;height:186px;background:var(--footer);color:#fff}
.follow{position:absolute;right:115px;top:38px;display:flex;align-items:center;gap:8px;font-size:10px}
.follow i{width:19px;height:19px;display:block;background:var(--blue);border-radius:2px}
.f-nav{position:absolute;left:407px;top:80px;display:flex;gap:18px;font-size:10.5px}
.f-line{position:absolute;left:113px;right:113px;top:120px;height:1px;background:#444}
.copy{position:absolute;left:0;right:0;top:150px;text-align:center;font-size:11px}
</style>
</head>
<body>

<!-- Page: program with video -->
<section class="page p1">
  <div class="photo photo-bg" role="img" aria-label="Woman with arms outstretched on a rock in a calm lake at sunrise"></div>
  <div class="brand" style="left:114px;top:18px"><span class="brand-dot"></span><span class="brand-name">Harbor<br>Lantern<br>Program</span></div>
  <div class="intro-box">
    <h2>Program</h2>
    <div class="intro-text">
      <p>“If you want to be busy and anxious, practice busy anxiousness. If you want to be calm and centered, practice it. It’s as simple as that.” (Dana Whitfield, Westbrook University mindfulness teacher and researcher)</p>
      <p>Well thanks Dana, sounds pretty simple...but what about when I’ve got 11 back-to-back meetings, a board meeting to prepare for with investors who have sky-high expectations, 6 new hires to onboard and 16 more to find, and–not least–a product to improve for the customers we are trying to serve and retain–only to wake up, rinse (maybe) and repeat tomorrow?? (We didn’t even mention the Relay and email messages mounting in the background.) How could I possibly exit “busy anxiousness” and practice calm centeredness amidst this chaos? (Notice what you feel just reading that–does your body tighten a bit?) Calm sounds nice–for vacation! I want results.</p>
    </div>
    <span class="btn">READ MORE</span>
    <div class="video" role="img" aria-label="Program video: a facilitator speaking to seated participants in a brick-walled room">
      <svg class="play" width="64" height="64" viewBox="0 0 64 64"><circle cx="32" cy="32" r="30" fill="#fff" opacity=".85"/><circle cx="32" cy="32" r="24" fill="#2f7fc8"/><path d="M26 20 L46 32 L26 44 Z" fill="#fff"/></svg>
    </div>
  </div>
</section>

<!-- Page: landing with image and words -->
<section class="page p2">
  <div class="photo photo-bg" role="img" aria-label="Woman breathing in with open arms in a green forest"></div>
  <div class="brand" style="left:407px;top:15px"><span class="brand-dot"></span><span class="brand-name" style="color:#4aa3e6;border-color:#4aa3e6">Harbor<br>Lantern<br>Program</span></div>
  <div class="landing-line">If your startup is growing rapidly,<br>we can help you do the same.<br>HLP: The ACTOR to AUTHOR Shift</div>
</section>

<!-- Page: home -->
<section class="page p3">
  <div class="hero" role="img" aria-label="Woman raising joined hands toward the sunset over coastal cliffs"></div>
  <div class="brand" style="left:114px;top:15px"><span class="brand-dot" style="width:56px;height:56px"></span><span class="brand-name" style="color:var(--navy);border-color:var(--navy);font-size:15px;line-height:16px">Harbor<br>Lantern<br>Program</span></div>
  <nav class="nav"><span class="on">HOME</span><span>PROGRAM</span><span>PROGRAM TIMELINE AND STRUCTURE</span><span>TESTIMONIALS</span><span>TEAM</span><span>FAQS</span></nav>
  <h1 class="hero-title">HARBOR LANTERN PROGRAM</h1>
  <span class="btn hero-btn">READ MORE</span>
  <div class="dots"><i></i><i></i><i class="on"></i><i></i><i></i></div>

  <div class="timeline">
    <div class="sec-title" style="top:34px">PROGRAM TIMELINE</div>
    <div class="rule" style="top:71px"></div>
    <svg class="arrow" style="left:62px" width="16" height="28" viewBox="0 0 16 28"><path d="M13 2 L3 14 L13 26" fill="none" stroke="#2f6fb0" stroke-width="2.5"/></svg>
    <svg class="arrow" style="left:957px" width="16" height="28" viewBox="0 0 16 28"><path d="M3 2 L13 14 L3 26" fill="none" stroke="#2f6fb0" stroke-width="2.5"/></svg>
    <div class="t-card" style="left:112px"><div class="t-head">MONTH 1</div><div class="t-body">
      <span class="t-week">Week 1</span><div class="t-item">Kickoff Orientation Workshop</div>
      <span class="t-week" style="margin-top:20px">Week 2</span><div class="t-item">1on1 Exec Coaching Session</div>
      <span class="t-week" style="margin-top:20px">Week 3</span><div class="t-item">Workshop</div></div></div>
    <div class="t-card" style="left:390px"><div class="t-head">MONTH 2</div><div class="t-body">
      <span class="t-week">Week 1</span><div class="t-item">1st Retreat (“Leading Yourself”)</div>
      <span class="t-week" style="margin-top:20px">Week 2</span><div class="t-item">1on1 Exec Coaching Session</div>
      <span class="t-week" style="margin-top:20px">Week 4</span><div class="t-item">Workshop</div></div></div>
    <div class="t-card" style="left:663px"><div class="t-head">MONTH 3</div><div class="t-body" style="padding-top:42px">
      <span class="t-week">Week 2</span><div class="t-item">1on1 Exec Coaching Session</div>
      <span class="t-week" style="margin-top:20px">Week 4</span><div class="t-item">Workshop</div></div></div>
  </div>

  <div class="logic">
    <div class="photo" role="img" aria-label="Workshop participants seated in rows listening to a facilitator"></div>
    <h3>THE LOGIC BEHIND THE STRUCTURE</h3>
    <div class="l-rule"></div>
    <div class="logic-text">
      <p>The retreat environment creates an immersive experience, co-created by the group. The sharp distinction from the fast pace of everyday startup life helps participants stand outside their everyday habits and evaluate which ones they want to change. Furthermore, just like in learning a language, immersion is the most powerful context for learning and ingraining new habits.</p>
      <p>Even so, we are wary of the format taken by many retreats/bootcamps which focus on just this one-off peak experience, neither sowing the seeds beforehand nor offering follow-up support for integrating the new insights and practices back in the regular world. Our workshops and coaching structure complements the work of the retreats, addressing both the before and after, sowing the seeds and watering the growing plant.</p>
    </div>
    <span class="btn">READ MORE</span>
  </div>

  <div class="team">
    <div class="sec-title" style="top:38px">OUR TEAM</div>
    <div class="rule" style="top:80px"></div>
    <div class="m-card" style="left:112px"><div class="photo" role="img" aria-label="Portrait of team member in a light blue shirt" style="background:linear-gradient(#9fb8cf,#4f7ea8)"></div>
      <div class="m-name">ROWAN</div><div class="m-role">CEO</div><div class="m-bio">Lorem Ipsum is simply dummy text of the printing and type setting industry lorem.</div><span class="btn">VIEW BIO</span></div>
    <div class="m-card" style="left:316px"><div class="photo" role="img" aria-label="Portrait of team member in a navy suit" style="background:linear-gradient(#c3d3e3,#2d4a78)"></div>
      <div class="m-name">PAUL BRENN</div><div class="m-role">Employee</div><div class="m-bio">Lorem Ipsum is simply dummy text of the printing and type setting industry lorem.</div><span class="btn">VIEW BIO</span></div>
    <div class="m-card" style="left:521px"><div class="photo" role="img" aria-label="Portrait of team member in a pink blouse" style="background:linear-gradient(#e4dcd8,#caa9b0)"></div>
      <div class="m-name">MIRA STONE</div><div class="m-role">Employee</div><div class="m-bio">Lorem Ipsum is simply dummy text of the printing and type setting industry lorem.</div><span class="btn">VIEW BIO</span></div>
    <div class="m-card" style="left:726px"><div class="photo" role="img" aria-label="Portrait of team member in an office" style="background:linear-gradient(#8a8f93,#a8c4d4)"></div>
      <div class="m-name">SELENE</div><div class="m-role">Employee</div><div class="m-bio">Lorem Ipsum is simply dummy text of the printing and type setting industry lorem.</div><span class="btn">VIEW BIO</span></div>
  </div>

  <div class="testi">
    <div class="sec-title">TESTIMONIALS</div>
    <div class="rule"></div>
    <svg class="arrow" style="left:64px;top:145px" width="16" height="28" viewBox="0 0 16 28"><path d="M13 2 L3 14 L13 26" fill="none" stroke="#fff" stroke-width="2.5"/></svg>
    <svg class="arrow" style="left:955px;top:145px" width="16" height="28" viewBox="0 0 16 28"><path d="M3 2 L13 14 L3 26" fill="none" stroke="#fff" stroke-width="2.5"/></svg>
    <p class="testi-text">Lorem ipsum dolor sit amet, consectetur adipiscing elit, sed do eiusmod tempor incididunt ut labore et dolore magna aliqua. Ut enim ad minim veniam, quis nostrud exercitation ullamco laboris nisi ut aliquip ex ea commodo consequat. Duis aute irure dolor in reprehenderit in voluptate velit esse cillum dolore eu fugiat nulla pariatur. Excepteur sint occaecat cupidatat non proident.</p>
    <div class="avatar" role="img" aria-label="Client portrait"></div>
    <div class="testi-name">ROWAN</div>
  </div>

  <footer class="footer">
    <div class="brand" style="left:114px;top:15px"><span class="brand-dot"></span><span class="brand-name">Harbor<br>Lantern<br>Program</span></div>
    <div class="follow">FOLLOW US <i></i><i></i><i></i></div>
    <nav class="f-nav"><span>HOME</span><span>PROGRAM</span><span>PROGRAM TIMELINE AND STRUCTURE</span><span>TESTIMONIALS</span><span>TEAM</span><span>FAQS</span></nav>
    <div class="f-line"></div>
    <div class="copy">Copyright © 2022 All Rights Reserved</div>
  </footer>
</section>

</body>
</html>
```